Business Card For Halvenmoor Financial Consulting

Hi, I would like a business card designed. Bold, modern.
Please use the same design as the logo. I have also attached the website design to see the overall theme.
Wordmark Font
Color: Hex: #01AEF7

```html
<!DOCTYPE html>
<html lang="en">
<head>
<meta charset="utf-8">
<title>Halvenmoor Financial Consulting – Business Card</title>
<link href="https://fonts.googleapis.com/css2?family=Open+Sans:wght@400;600;700&display=swap" rel="stylesheet">
<style>
  :root {
    --stage: #232323;
    --navy: #0b4570;
    --navy-deep: #083a60;
    --sky: #34a9e0;
    --sky-pale: #d9e9f7;
    --paper: #ffffff;
    --ink: #1d1d1d;
  }
  * { margin: 0; padding: 0; box-sizing: border-box; }
  html, body {
    width: 1200px; height: 780px; overflow: hidden;
    background: var(--stage);
    font-family: "Open Sans", Arial, sans-serif;
  }
  .canvas { position: relative; width: 1200px; height: 780px; }

  .card {
    position: absolute; top: 235px;
    width: 540px; height: 310px;
    overflow: hidden;
    box-shadow: 0 18px 40px rgba(0,0,0,.55);
  }
  .card--front { left: 40px; background: var(--paper); }
  .card--back { left: 620px; background: var(--navy); }

  .brand { position: absolute; display: flex; align-items: center; gap: 10px; }
  .brand__mark { width: 22px; height: 22px; border: 3px solid var(--sky); }
  .brand__name { font-weight: 700; font-size: 19px; letter-spacing: .5px; }
  .card--front .brand { left: 30px; top: 28px; }
  .card--front .brand__name { color: var(--navy); }
  .card--back .brand { right: 34px; bottom: 40px; }
  .card--back .brand__name { color: var(--paper); }

  .holder { position: absolute; right: 40px; top: 112px; text-align: right; }
  .holder__name { font-size: 28px; font-weight: 700; line-height: 1.1; }
  .holder__first { color: var(--sky); }
  .holder__last { color: var(--navy); }
  .holder__title { font-size: 15px; color: var(--ink); margin-top: 2px; }

  .divider {
    position: absolute; left: 30px; right: 30px; top: 182px;
    height: 1.5px; background: var(--navy);
  }
  .accent-tab {
    position: absolute; right: 0; top: 172px;
    width: 12px; height: 24px; background: var(--sky);
  }

  .contact {
    position: absolute; left: 30px; top: 194px;
    font-size: 12.5px; color: var(--ink); line-height: 1.45;
    list-style: none;
  }
  .contact li { display: flex; align-items: center; gap: 6px; }
  .contact__address { margin-bottom: 2px; }
  .contact svg { width: 11px; height: 11px; flex: none; }

  .swoosh { position: absolute; left: 0; bottom: 0; width: 540px; height: 310px; pointer-events: none; }
</style>
</head>
<body>
<main class="canvas">

  <section class="card card--front" aria-label="Business card, front">
    <svg class="swoosh" viewBox="0 0 540 310" aria-hidden="true">
      <path d="M0 292 C180 300 380 280 540 200 L540 216 C380 292 180 310 0 304 Z" fill="var(--sky)"/>
      <path d="M0 304 C180 310 380 292 540 216 L540 310 L0 310 Z" fill="var(--navy)"/>
    </svg>

    <div class="brand">
      <span class="brand__mark"></span>
      <span class="brand__name">Halvenmoor Financial Consulting</span>
    </div>

    <div class="holder">
      <div class="holder__name"><span class="holder__first">Marta</span> <span class="holder__last">Lindqvist</span></div>
      <div class="holder__title">Managing Director</div>
    </div>

    <div class="divider"></div>
    <div class="accent-tab"></div>

    <ul class="contact">
      <li class="contact__address">1840 Ridgeline Ave. Suite 300<br>Cedar Falls, TX 76540</li>
      <li>
        <svg viewBox="0 0 12 12"><path d="M2.5 1 L4.5 1 L5.3 3.4 L4 4.4 C4.6 5.8 6.2 7.4 7.6 8 L8.6 6.7 L11 7.5 L11 9.5 C11 10.3 10.3 11 9.5 11 C5 11 1 7 1 2.5 C1 1.7 1.7 1 2.5 1 Z" fill="var(--sky)"/></svg>
        (555) 214-0387
      </li>
      <li>
        <svg viewBox="0 0 12 12"><rect x="1" y="2.5" width="10" height="7" rx="1" fill="var(--sky)"/><path d="M1.5 3 L6 6.5 L10.5 3" stroke="#fff" stroke-width="1" fill="none"/></svg>
        info@halvenmoorfc.com
      </li>
      <li>
        <svg viewBox="0 0 12 12"><circle cx="6" cy="6" r="5" fill="var(--sky)"/><path d="M1 6 H11 M6 1 C3.5 3.5 3.5 8.5 6 11 M6 1 C8.5 3.5 8.5 8.5 6 11" stroke="#fff" stroke-width=".8" fill="none"/></svg>
        www.halvenmoorfc.com
      </li>
    </ul>
  </section>

  <section class="card card--back" aria-label="Business card, back">
    <div class="brand">
      <span class="brand__mark"></span>
      <span class="brand__name">Halvenmoor Financial Consulting</span>
    </div>
  </section>

</main>
</body>
</html>
```